Red Mesa Greenworks Summit needs a marketing flyer

We need a full page graphic for our upcoming Forum that can also be converted into a website "header" for social media, etc.: "Red Mesa Greenworks Summit - Shaping Change Across the Made Landscape"

INTRODUCTION:
During the first week of August 2022, Q-VarDT is presenting the Red Mesa Greenworks Summit - Shaping Change Across the Made Landscape.

One of the most exciting aspects of this conference will be the bringing together of multiple organizations including for-profits and nonprofits, K-12’s and higher education, cities and counties and other governmental agencies, as well as architects, engineers, and contractors to collaboratively present and discuss issues and ideas related to sustainability, with a Texas focus.

This event will be a catalyst for public and private project owners to holistically gather information and momentum as we bring the resources and vision needed to achieve the goal of zero carbon emissions from the built environment by 2040, and address water, green space and the natural environment, transportation, equity, and funding, among other topics.

```html
<!DOCTYPE html>
<html lang="en">
<head>
<meta charset="utf-8">
<title>Red Mesa Greenworks Summit – Flyer</title>
<link href="https://fonts.googleapis.com/css2?family=Poppins:wght@300;400;600;700&family=Russo+One&display=swap" rel="stylesheet">
<style>
  :root{
    --page:#ececee;
    --blue:#1f3e9c;
    --blue-deep:#16308a;
    --green:#8ab53d;
    --ink:#1b1b1d;
    --paper:#ffffff;
    --band:#e7e8eb;
    --photo-a:#8d8478;
    --photo-b:#c9a679;
  }
  *{margin:0;padding:0;box-sizing:border-box}
  html,body{width:1200px;height:1200px;overflow:hidden;background:var(--page)}
  body{display:flex;align-items:center;justify-content:center;font-family:'Poppins',sans-serif;color:var(--ink)}
  .flyer{position:relative;width:848px;height:1200px;background:var(--paper);overflow:hidden}
  .shapes{position:absolute;inset:0}
  .photo{position:absolute;left:422px;top:-60px;width:560px;height:560px;border-radius:50%;
    background:radial-gradient(circle at 45% 35%, #b9b2a6 0%, var(--photo-a) 45%, var(--photo-b) 85%);
    box-shadow:0 0 0 14px var(--green)}
  .brand{position:absolute;left:52px;top:58px;display:flex;align-items:center;gap:18px;color:var(--paper)}
  .brand-dot{width:78px;height:78px;border-radius:50%;background:var(--paper)}
  .brand-name{font-size:44px;font-weight:400;line-height:1;letter-spacing:1px}
  .brand-tag{font-size:11px;font-weight:400;margin-top:8px;padding-top:6px;border-top:1px solid var(--paper)}
  .title{position:absolute;left:56px;top:212px;font-family:'Russo One',sans-serif;line-height:.95;font-weight:400}
  .title .t1{display:block;color:var(--paper);font-size:58px}
  .title .t2{display:block;color:var(--green);font-size:42px;margin-top:4px}
  .title .t3{display:block;color:var(--green);font-size:78px;margin-top:2px}
  .when{position:absolute;left:52px;top:600px}
  .when-lead{font-size:30px;font-weight:400}
  .when-pill{display:flex;margin-top:6px;height:54px;border-radius:27px;overflow:hidden;width:max-content;background:var(--green)}
  .when-month{background:var(--blue);color:var(--paper);font-size:38px;font-weight:300;padding:0 22px;display:flex;align-items:center;border-radius:27px}
  .when-year{color:var(--paper);font-family:'Russo One',sans-serif;font-size:40px;padding:0 22px 0 16px;display:flex;align-items:center}
  .presenting{position:absolute;left:58px;top:740px;font-size:26px;font-weight:300;letter-spacing:5px;line-height:1.05;text-transform:uppercase}
  .presenting span{display:block;color:var(--blue)}
  .presenting-sub{position:absolute;left:60px;top:814px;width:380px;font-size:16px;line-height:1.35}
  .body-copy{position:absolute;left:60px;top:882px;width:400px;font-size:15.5px;line-height:1.38;text-align:justify}
  .topics{position:absolute;left:492px;top:586px;width:300px;color:var(--paper)}
  .topics-lead{font-size:16px;line-height:1.35;margin-bottom:20px}
  .topics ul{list-style:none}
  .topics li{display:flex;gap:10px;font-size:16px;font-weight:600;line-height:1.25;margin-bottom:14px}
  .tick{flex:0 0 18px;width:18px;height:18px;margin-top:2px}
  .contact{position:absolute;left:56px;top:1112px;font-size:17px}
  .contact-row{display:flex;align-items:center;gap:10px;margin-bottom:8px}
  .phone-num{font-weight:700;font-size:28px;line-height:1.1}
  .icon{width:24px;height:24px}
  .web{position:absolute;left:540px;top:1010px;width:240px;text-align:center;font-size:19px}
  .web svg{display:block;margin:0 auto 8px;width:30px;height:30px}
</style>
</head>
<body>
<main class="flyer">
  <svg class="shapes" viewBox="0 0 848 1200" aria-hidden="true">
    <path d="M0,0 H848 V470 C600,430 300,430 0,540 Z" fill="var(--blue)"/>
    <path d="M0,540 C300,430 600,430 848,470 V480 C600,460 300,470 0,600 Z" fill="var(--green)"/>
    <rect x="478" y="470" width="330" height="530" rx="22" fill="var(--green)"/>
    <path d="M0,1100 L560,1062 L520,1200 H0 Z" fill="var(--band)"/>
    <path d="M560,1200 C650,1125 750,1090 848,1083 V1107 C755,1115 670,1150 600,1200 Z" fill="var(--blue-deep)"/>
    <path d="M640,1200 C710,1165 780,1143 848,1139 V1149 C785,1155 720,1180 660,1200 Z" fill="var(--blue)"/>
  </svg>

  <div class="photo" role="img" aria-label="Photo of a team of professionals discussing around a meeting table with a laptop"></div>

  <div class="brand">
    <div class="brand-dot"></div>
    <div>
      <div class="brand-name">Q-VarDT</div>
      <div class="brand-tag">Institute for Vision in Design Trades</div>
    </div>
  </div>

  <h1 class="title">
    <span class="t1">RED MESA</span>
    <span class="t2">GREENWORKS</span>
    <span class="t3">SUMMIT</span>
  </h1>

  <div class="when">
    <p class="when-lead">During the first week of</p>
    <div class="when-pill"><span class="when-month">AUGUST</span><span class="when-year">2022</span></div>
  </div>

  <p class="presenting">Q-VarDT is <span>presenting</span></p>
  <p class="presenting-sub">the Red Mesa Greenworks Summit - Shaping Change Across</p>

  <p class="body-copy">This event will be a catalyst for public and private project owners to holistically gather information and momentum as we bring the resources and vision needed to achieve the goal of zero carbon emissions from the built environment by 2040, and address water, green space and the natural environment, transportation, equity, and funding, among other topics.</p>

  <section class="topics">
    <p class="topics-lead">One of the most exciting aspects of this conference will be the bringing together of multiple organizations including</p>
    <ul>
      <li><svg class="tick" viewBox="0 0 18 18"><circle cx="9" cy="9" r="9" fill="var(--blue)"/><path d="M5 9.5 L8 12 L13 6" stroke="#fff" stroke-width="2" fill="none"/></svg>Profits and nonprofits</li>
      <li><svg class="tick" viewBox="0 0 18 18"><circle cx="9" cy="9" r="9" fill="var(--blue)"/><path d="M5 9.5 L8 12 L13 6" stroke="#fff" stroke-width="2" fill="none"/></svg>K-12’s and higher education</li>
      <li><svg class="tick" viewBox="0 0 18 18"><circle cx="9" cy="9" r="9" fill="var(--blue)"/><path d="M5 9.5 L8 12 L13 6" stroke="#fff" stroke-width="2" fill="none"/></svg>Cities and counties and other governmental agencies</li>
      <li><svg class="tick" viewBox="0 0 18 18"><circle cx="9" cy="9" r="9" fill="var(--blue)"/><path d="M5 9.5 L8 12 L13 6" stroke="#fff" stroke-width="2" fill="none"/></svg>As well as architects</li>
      <li><svg class="tick" viewBox="0 0 18 18"><circle cx="9" cy="9" r="9" fill="var(--blue)"/><path d="M5 9.5 L8 12 L13 6" stroke="#fff" stroke-width="2" fill="none"/></svg>Engineers</li>
      <li><svg class="tick" viewBox="0 0 18 18"><circle cx="9" cy="9" r="9" fill="var(--blue)"/><path d="M5 9.5 L8 12 L13 6" stroke="#fff" stroke-width="2" fill="none"/></svg>Contractors to collaboratively</li>
      <li><svg class="tick" viewBox="0 0 18 18"><circle cx="9" cy="9" r="9" fill="var(--blue)"/><path d="M5 9.5 L8 12 L13 6" stroke="#fff" stroke-width="2" fill="none"/></svg>present and discuss issues and ideas related to sustainability</li>
      <li><svg class="tick" viewBox="0 0 18 18"><circle cx="9" cy="9" r="9" fill="var(--blue)"/><path d="M5 9.5 L8 12 L13 6" stroke="#fff" stroke-width="2" fill="none"/></svg>With a Texas focus.</li>
    </ul>
  </section>

  <div class="contact">
    <div class="contact-row">
      <svg class="icon" viewBox="0 0 24 24"><path d="M6.6 10.8a15 15 0 0 0 6.6 6.6l2.2-2.2a1 1 0 0 1 1-.25 11.4 11.4 0 0 0 3.6.57 1 1 0 0 1 1 1V20a1 1 0 0 1-1 1A17 17 0 0 1 3 4a1 1 0 0 1 1-1h3.5a1 1 0 0 1 1 1c0 1.25.2 2.45.57 3.57a1 1 0 0 1-.25 1Z" fill="var(--blue)"/></svg>
      <span class="phone-num">1234567890</span>
    </div>
    <div class="contact-row">
      <svg class="icon" viewBox="0 0 24 24"><rect x="2" y="5" width="20" height="14" rx="1" fill="var(--blue)"/><path d="M3 6 L12 13 L21 6" stroke="#fff" stroke-width="1.6" fill="none"/></svg>
      <span>info@qvardtforum.com</span>
    </div>
  </div>

  <div class="web">
    <svg viewBox="0 0 30 30"><circle cx="15" cy="15" r="13" fill="var(--blue)"/><g stroke="#fff" stroke-width="1.4" fill="none"><ellipse cx="15" cy="15" rx="6" ry="13"/><path d="M2 15 H28 M4 8.5 H26 M4 21.5 H26 M15 2 V28"/></g></svg>
    www.qvardtforum.com
  </div>
</main>
</body>
</html>
```